Redesign of LumoWordfind.com in Bootstrap 4

Current design of LumoWordfind.com is not responsive. We need to change it to latest version of Bootstrap 4 keeping essential elements in place.

Apart from home page, we need designs for http://www.lumowordfind.com/meaning/cat also.

Coding

Number of Pages Required

2 page

Colors
34a7d8

Requirements
Must have
• Bootstrap 4

```html
<!DOCTYPE html>
<html lang="en">
<head>
<meta charset="utf-8">
<title>Lumo Wordfind – English Dictionary</title>
<link href="https://fonts.googleapis.com/css2?family=Open+Sans:wght@400;600;700&display=swap" rel="stylesheet">
<style>
:root{
  --brand:#34a7d8;
  --brand-deep:#2589b6;
  --accent:#f7a11a;
  --ink:#222;
  --soft:#f4f4f4;
  --white:#fff;
  --floor:#8b7a66;
  --shelf:#5e4a36;
  --denim:#2f4260;
  --bee:#f2bd22;
}
*{box-sizing:border-box;margin:0;padding:0}
html,body{width:710px;height:1200px;overflow:hidden}
body{font-family:"Open Sans",Arial,sans-serif;color:var(--ink);background:var(--white);position:relative}
a{color:inherit;text-decoration:none}

/* header */
.site-header{position:absolute;left:0;top:0;width:710px;height:66px;background:var(--white);border-top:2px solid var(--brand)}
.brand{position:absolute;left:78px;top:16px;display:flex;align-items:center;gap:6px;font-weight:700;font-size:16px;color:var(--brand)}
.brand-dot{width:12px;height:12px;border-radius:50%;background:var(--accent)}
.auth-btn{position:absolute;top:9px;height:19px;background:var(--brand);color:var(--white);font-size:9px;line-height:19px;text-align:center;border-radius:2px}
.main-nav{position:absolute;top:44px;left:0;width:710px;font-size:9px;color:#444}
.main-nav a{position:absolute;top:0}
.main-nav .active{color:var(--brand)}
.main-nav .active::after{content:"";position:absolute;left:-2px;right:-2px;top:20px;height:2px;background:var(--brand)}

/* hero */
.hero{position:absolute;left:0;top:66px;width:710px;height:259px;
  background:
    linear-gradient(160deg,rgba(47,66,96,0) 55%,rgba(47,66,96,.85) 80%),
    linear-gradient(180deg,var(--shelf) 0%,#7a6a58 18%,var(--floor) 45%,#6e5f50 100%)}
.hero-arrow{position:absolute;top:118px;width:10px;height:18px}
.hero-box{position:absolute;left:194px;top:66px;width:322px;height:117px;background:rgba(255,255,255,.82)}
.hero-title{position:absolute;left:0;width:100%;top:13px;text-align:center;color:var(--brand);font-size:18px;font-weight:600}
.hero-sub{position:absolute;left:0;width:100%;top:42px;text-align:center;color:#444;font-size:10px}
.search-bar{position:absolute;left:22px;top:63px;width:278px;height:31px;background:var(--accent);display:flex;align-items:center;padding:0 3px}
.search-label{color:var(--white);font-size:9px;width:43px;padding-left:7px}
.search-input{flex:0 0 205px;height:22px;background:var(--white)}
.search-icon{flex:1;display:flex;justify-content:center}

/* features */
.features{position:absolute;left:0;top:325px;width:710px;height:206px;background:var(--soft)}
.mascot{position:absolute;left:66px;top:30px;width:88px;height:132px;border-radius:44px 44px 30px 30px;background:linear-gradient(180deg,var(--bee) 0%,#e9a91c 55%,#3a3220 100%)}
.features h2{position:absolute;left:182px;top:36px;font-size:17px;font-weight:600;color:var(--brand)}
.feature-list{position:absolute;left:182px;top:69px;list-style:none;font-size:8px;color:#666;line-height:13.2px}
.addon-btn{position:absolute;left:182px;top:153px;height:22px;width:96px;background:var(--brand);color:var(--white);font-size:8.5px;border-radius:2px;display:flex;align-items:center;padding-left:6px;gap:5px}
.addon-dot{width:14px;height:14px;border-radius:50%;background:var(--white);opacity:.9}
.wotd{position:absolute;left:457px;top:33px;width:174px;height:129px;background:var(--white);border:1px solid #d6d6d6}
.wotd-head{height:32px;background:var(--brand);color:var(--white);font-size:11px;font-weight:600;text-align:center;line-height:32px}
.wotd-word{position:absolute;top:46px;left:0;width:100%;text-align:center;font-size:17px;font-weight:600;color:var(--ink)}
.wotd-phon{position:absolute;top:75px;left:0;width:100%;text-align:center;font-size:8px;color:#333}
.wotd-btn{position:absolute;left:42px;top:92px;width:85px;height:21px;background:var(--brand);color:var(--white);font-size:8.5px;line-height:21px;text-align:center;border-radius:2px}

/* word finder */
.finder{position:absolute;left:0;top:531px;width:710px;height:247px;
  background:
    radial-gradient(ellipse 160px 120px at 410px 125px,rgba(225,240,250,.75),rgba(225,240,250,0) 70%),
    linear-gradient(100deg,#2e9ed3 0%,#6dbde3 45%,#4fa9d8 100%)}
.finder-card{position:absolute;left:78px;top:33px;width:174px;height:181px;background:rgba(255,255,255,.82)}
.finder-card h2{position:absolute;left:16px;top:17px;font-size:17px;font-weight:400;color:var(--brand)}
.finder-text{position:absolute;left:16px;top:48px;width:148px;font-size:7.5px;line-height:13px;color:#555}
.finder-links{position:absolute;left:13px;top:92px;font-size:8.5px;line-height:14px;color:var(--brand)}
.finder-btn{position:absolute;left:13px;top:131px;width:80px;height:22px;background:var(--brand);color:var(--white);font-size:8.5px;line-height:22px;text-align:center;border-radius:2px}

/* blog */
.blog{position:absolute;left:0;top:778px;width:710px;height:236px;background:var(--soft)}
.blog h2{position:absolute;left:77px;top:23px;font-size:17px;font-weight:400;color:var(--brand)}
.post{position:absolute;top:64px;width:169px}
.post-image{width:169px;height:86px;border:2px solid var(--white);box-shadow:0 0 0 1px #ddd}
.post-image.island{background:linear-gradient(180deg,#9fd6ee 0%,#6cbfe2 60%,#e4c98f 78%,#48a6d4 100%)}
.post-image.palms{background:linear-gradient(180deg,#8fd0ec 0%,#5fb6df 70%,#3f8fb8 100%)}
.post-image.hallway{background:linear-gradient(90deg,#8c7d6c 0%,#b3a390 50%,#6d6153 100%)}
.post-title{margin-top:9px;font-size:12px;line-height:17px;color:var(--brand);font-weight:400}
.post-meta{margin-top:9px;font-size:7.5px;color:#666}

/* footer */
.site-footer{position:absolute;left:0;top:1014px;width:710px;height:148px;background:var(--brand);color:var(--white)}
.footer-col{position:absolute;top:19px}
.footer-col h3{font-size:11.5px;font-weight:400;margin-bottom:7px}
.footer-col ul{list-style:none;font-size:7px;line-height:13.3px}
.newsletter p{font-size:7px;line-height:13px;width:140px}
.mail-field{margin-top:10px;width:125px;height:22px;background:var(--white);color:#333;font-size:6.5px;display:flex;align-items:center;padding-left:8px;gap:5px;border-radius:2px}
.submit-btn{margin-top:11px;width:42px;height:18px;background:#111;color:var(--white);font-size:7px;line-height:18px;text-align:center;border-radius:2px}
.footer-brand{position:absolute;left:560px;top:25px;font-size:13px;font-weight:700}
.socials{position:absolute;left:558px;top:61px;display:flex;gap:3px}
.socials span{width:13px;height:13px;border:1px solid var(--white);border-radius:50%}
.copyright{position:absolute;left:0;top:1162px;width:710px;height:38px;background:var(--brand-deep);color:var(--white);font-size:7px;text-align:center;line-height:38px}
</style>
</head>
<body>

<header class="site-header">
  <a class="brand" href="#"><span class="brand-dot"></span>Lumo Wordfind</a>
  <a class="auth-btn" href="#" style="left:530px;width:43px">Login</a>
  <a class="auth-btn" href="#" style="left:579px;width:54px">Register</a>
  <nav class="main-nav">
    <a class="active" href="#" style="left:272px">Home</a>
    <a href="#" style="left:327px">Idioms</a>
    <a href="#" style="left:385px">Common Errors</a>
    <a href="#" style="left:479px">Crossword</a>
    <a href="#" style="left:553px">Blog</a>
    <a href="#" style="left:601px">Contact</a>
  </nav>
</header>

<section class="hero" role="img" aria-label="Photo of a student reading a book and typing on a laptop between library shelves">
  <svg class="hero-arrow" style="left:42px" viewBox="0 0 10 18"><path d="M9 1 1 9l8 8" fill="none" stroke="#fff" stroke-width="1.3" opacity=".8"/></svg>
  <svg class="hero-arrow" style="left:658px" viewBox="0 0 10 18"><path d="M1 1l8 8-8 8" fill="none" stroke="#fff" stroke-width="1.3" opacity=".8"/></svg>
  <div class="hero-box">
    <h1 class="hero-title">Lumo English Dictionary</h1>
    <p class="hero-sub">Clear. Clean. Uncluttered.</p>
    <form class="search-bar">
      <span class="search-label">Search</span>
      <span class="search-input"></span>
      <span class="search-icon"><svg width="11" height="11" viewBox="0 0 12 12"><circle cx="5" cy="5" r="3.8" fill="none" stroke="#fff" stroke-width="1.8"/><path d="M8 8l3 3" stroke="#fff" stroke-width="2"/></svg></span>
    </form>
  </div>
</section>

<section class="features">
  <div class="mascot" role="img" aria-label="Cartoon bee mascot giving a thumbs up"></div>
  <h2>Search, Save and Master Words</h2>
  <ul class="feature-list">
    <li>Search from more than 300,000 words and phrases</li>
    <li>Multiple usages to clarify the context</li>
    <li>Audio, phonetics, meanings, synonyms and antonyms</li>
    <li>Save the words to your personal deck and access from anywhere</li>
    <li>It's FREE</li>
  </ul>
  <a class="addon-btn" href="#"><span class="addon-dot"></span>Browser Addon</a>
  <aside class="wotd">
    <div class="wotd-head">Word of the Day</div>
    <div class="wotd-word">exhaustive
      <svg width="12" height="11" viewBox="0 0 12 11" style="vertical-align:1px;margin-left:4px"><path d="M1 4h2l3-3v9L3 7H1z" fill="#222"/><path d="M8 3.5q1.5 2 0 4M9.5 2q3 3.5 0 7" fill="none" stroke="#222" stroke-width="1"/></svg>
    </div>
    <div class="wotd-phon">/ Ig ' zc stiv &nbsp;/</div>
    <a class="wotd-btn" href="#">Show Definition</a>
  </aside>
</section>

<section class="finder" role="img" aria-label="Close-up of dictionary print seen through a magnifying glass, in blue tones">
  <div class="finder-card">
    <h2>Word Finder</h2>
    <p class="finder-text">Neque porro quisquam est qui dolorem ipsum quia dolor sit amet, consectetur, adipisci velit...</p>
    <div class="finder-links"><a href="#">Tile Game Word Finder</a><br><a href="#">Word Pals Cheat</a></div>
    <a class="finder-btn" href="#">Try Word Finder</a>
  </div>
</section>

<section class="blog">
  <h2>Recent Blog</h2>
  <article class="post" style="left:78px">
    <div class="post-image island" role="img" aria-label="Comic strip about a desert island"></div>
    <h3 class="post-title">Meaning and usage of<br>asphyxiation</h3>
    <p class="post-meta">April 16, 2014 by Ann</p>
  </article>
  <article class="post" style="left:271px">
    <div class="post-image palms" role="img" aria-label="Comic strip about searching for the truth"></div>
    <h3 class="post-title">Meaning of existential and<br>its usage</h3>
    <p class="post-meta">April 16, 2014 by Ann</p>
  </article>
  <article class="post" style="left:464px">
    <div class="post-image hallway" role="img" aria-label="Comic strip of two men talking in a hallway"></div>
    <h3 class="post-title">Prosody – What does this<br>mean?</h3>
    <p class="post-meta">April 16, 2014 by Ann</p>
  </article>
</section>

<footer class="site-footer">
  <div class="footer-col" style="left:78px">
    <h3>Quick Links</h3>
    <ul><li>Home</li><li>Idioms</li><li>Common Errors</li><li>Crossword</li><li>Blog</li><li>Contact</li></ul>
  </div>
  <div class="footer-col" style="left:176px">
    <h3>Company</h3>
    <ul><li>FAQ</li><li>Contact</li><li>Blog</li><li>Privacy Policy</li><li>Terms of Use</li></ul>
  </div>
  <div class="footer-col newsletter" style="left:278px">
    <h3>Newsletter</h3>
    <p>Subscribe newsletter to receive the latest updates direct to your inbox.</p>
    <div class="mail-field"><svg width="8" height="6" viewBox="0 0 8 6"><rect x=".5" y=".5" width="7" height="5" fill="none" stroke="#333" stroke-width=".8"/><path d="M.5.5 4 3.5 7.5.5" fill="none" stroke="#333" stroke-width=".8"/></svg>Enter Your Mail Id</div>
    <div class="submit-btn">Submit</div>
  </div>
  <div class="footer-col" style="left:446px">
    <h3>Others</h3>
    <ul><li>Popular Words</li><li>Common Errors in English</li><li>Exam Prep Online</li></ul>
  </div>
  <div class="footer-brand">Lumo Wordfind</div>
  <div class="socials"><span></span><span></span><span></span><span></span><span></span></div>
</footer>
<div class="copyright">Copyright © 2016 lumowordfind.com. All rights reserved.</div>

</body>
</html>
```